Business card design for my company.
I would like the card's background colour to be black. You can also see our web site to get an idea of our brand. https://www.tmwhomecrafting.com.au/
- Name
- Email

```html
<!DOCTYPE html>
<html lang="en">
<head>
<meta charset="utf-8">
<title>TMW Home Crafting – Business Card</title>
<link rel="stylesheet" href="https://fonts.googleapis.com/css2?family=Arimo:wght@400;700&display=swap">
<style>
  :root {
    --page-bg: #e4e4e4;
    --card-bg: #2f2f2f;
    --brand-green: #0f9444;
    --text-light: #f2f2f4;
    --emboss: #3b3b3b;
  }
  * { margin: 0; padding: 0; box-sizing: border-box; }
  html, body { width: 1200px; height: 1200px; overflow: hidden; }
  body {
    background: var(--page-bg);
    font-family: "Arimo", Arial, sans-serif;
    position: relative;
  }
  .card {
    position: absolute;
    width: 688px;
    height: 393px;
    background: var(--card-bg);
    color: var(--text-light);
  }
  .card--front { left: 266px; top: 158px; }
  .card--back  { left: 262px; top: 653px; }

  .holder { position: absolute; left: 44px; top: 66px; }
  .holder__name {
    color: var(--brand-green);
    font-weight: 700;
    font-size: 25px;
    letter-spacing: 0.2px;
    line-height: 1;
  }
  .holder__title { font-size: 15px; margin-top: 8px; }

  .address {
    position: absolute; left: 44px; top: 202px;
    font-size: 16px; line-height: 21px; font-style: normal;
  }
  .contacts {
    position: absolute; left: 44px; top: 265px;
    list-style: none; font-size: 16px;
  }
  .contacts li {
    display: flex; align-items: center;
    height: 20.5px;
  }
  .contacts svg { width: 14px; height: 14px; margin-right: 12px; fill: var(--brand-green); }

  .brand-emboss {
    position: absolute; right: 28px; top: 248px;
    font-weight: 700; font-size: 34px; line-height: 1.05;
    color: var(--emboss); text-align: right;
  }

  .brand {
    position: absolute; inset: 0;
    display: flex; align-items: center; justify-content: center; gap: 16px;
  }
  .brand__mark { width: 26px; height: 26px; background: var(--brand-green); }
  .brand__name {
    font-weight: 700; font-size: 42px; color: var(--text-light);
    letter-spacing: 0.5px;
  }
</style>
</head>
<body>
  <section class="card card--front">
    <div class="holder">
      <p class="holder__name">DANIEL REYES</p>
      <p class="holder__title">President</p>
    </div>
    <address class="address">
      412 Harbour View Road<br>
      Brookvale, NSW 2100
    </address>
    <ul class="contacts">
      <li><svg viewBox="0 0 24 24" aria-hidden="true"><path d="M6.6 10.8a15.2 15.2 0 0 0 6.6 6.6l2.2-2.2a1 1 0 0 1 1-.25 11.4 11.4 0 0 0 3.6.57 1 1 0 0 1 1 1V20a1 1 0 0 1-1 1A17 17 0 0 1 3 4a1 1 0 0 1 1-1h3.5a1 1 0 0 1 1 1c0 1.25.2 2.45.57 3.57a1 1 0 0 1-.25 1z"/></svg>555-210-4187</li>
      <li><svg viewBox="0 0 24 24" aria-hidden="true"><path d="M7 1h10a2 2 0 0 1 2 2v18a2 2 0 0 1-2 2H7a2 2 0 0 1-2-2V3a2 2 0 0 1 2-2zm0 3v15h10V4zm5 16.2a1 1 0 1 0 0 .1z"/></svg>555-382-9061</li>
      <li><svg viewBox="0 0 24 24" aria-hidden="true"><path d="M2 5h20v14H2zm2 2v.5l8 5 8-5V7z"/></svg>info@tmwhomecrafting.com.au</li>
      <li><svg viewBox="0 0 24 24" aria-hidden="true"><circle cx="12" cy="12" r="10"/></svg>www.tmwhomecrafting.com.au</li>
    </ul>
    <p class="brand-emboss">TMW<br>HOME CRAFTING</p>
  </section>

  <section class="card card--back">
    <div class="brand">
      <span class="brand__mark"></span>
      <span class="brand__name">TMW Home Crafting</span>
    </div>
  </section>
</body>
</html>
```